Business Cards Needed for Innovative Healthcare Marketing Company

We are a marketing company focused on healthcare. Our company is all about rebranding yourself renewing your image and generating results. The phoenix stands for "reborn" or "rising" which we provide new brands for our clients we take their old brands and renew it with creativity and innovation. I am looking for a business card with color dimension. I have attached an example of a card I think has the look and feel of what I am trying to accomplish. I like that the card example has black and grey font colors, I like the font placement and the small logo, I really like the use of the colors on the right those are the colors of my logo. My logo is phoenix so maybe incorporating flames similar to that design. I would like the back a solid color maybe red with an opaque version of the logo and website. As a marketing company I am always open to creative liberty!

Target Market(s)

Doctors and business professionals.

Industry/Entity Type

Marketing

Contact Information for Business Card

Valcorne Health Care Marketing
Marla Tenwick- CEO
#(512)638-2974
email-marla@valcorne.com
website- valcorne.com

Font styles to use
Sans Serif

Colors
ec1f27
f37122
ffc214
fbed22
fbf289
f04a50

Requirements
Must have
• The logo and required information
Nice to have
• icons by the information
Should not have
• child like font

```html
<!DOCTYPE html>
<html lang="en">
<head>
<meta charset="utf-8">
<title>Valcorne Health Care Marketing – Business Card</title>
<link rel="stylesheet" href="https://fonts.googleapis.com/css2?family=Questrial&display=swap">
<style>
  :root {
    --page-bg: #efe9e1;
    --card-white: #ffffff;
    --brand-red: #a31f22;
    --brand-red-text: #a8232a;
    --ink: #161616;
    --flame-rust: #bf4a32;
    --flame-crimson: #a3302c;
    --flame-deep: #a22424;
    --flame-orange: #f29a28;
    --flame-amber: #e0702a;
    --back-mark: #c4474d;
  }
  * { margin: 0; padding: 0; box-sizing: border-box; }
  html, body { width: 1181px; height: 1200px; overflow: hidden; }
  body {
    background: var(--page-bg);
    font-family: "Questrial", sans-serif;
    position: relative;
  }
  .card {
    position: absolute;
    width: 723px;
    height: 454px;
    border-radius: 18px;
    overflow: hidden;
  }
  .card-front { left: 233px; top: 98px; background: var(--card-white); }
  .card-back  { left: 230px; top: 646px; background: var(--brand-red); }

  .flames { position: absolute; inset: 0; }

  .brand { position: absolute; left: 29px; top: 70px; display: flex; align-items: center; gap: 14px; }
  .brand-dot { width: 52px; height: 52px; border-radius: 50%; background: var(--flame-amber); }
  .brand-name { color: var(--brand-red-text); font-size: 24px; letter-spacing: 1px; }

  .person { position: absolute; left: 31px; top: 242px; }
  .person-name { color: var(--ink); font-size: 29px; line-height: 1; }
  .person-role { color: var(--brand-red-text); font-size: 21px; margin-top: 6px; line-height: 1; }

  .contacts { position: absolute; left: 34px; top: 315px; list-style: none; }
  .contacts li { display: flex; align-items: center; height: 34px; font-size: 19.5px; color: var(--ink); }
  .contacts svg { width: 20px; height: 16px; margin-right: 12px; fill: var(--brand-red-text); }

  .back-mark { position: absolute; left: 0; right: 0; top: 150px; display: flex; justify-content: center; align-items: center; gap: 28px; }
  .back-dot { width: 110px; height: 110px; border-radius: 50%; background: var(--back-mark); }
  .back-name { color: var(--back-mark); font-size: 92px; letter-spacing: 3px; line-height: 1; }
</style>
</head>
<body>
  <section class="card card-front" aria-label="Business card front">
    <svg class="flames" viewBox="0 0 723 454" aria-hidden="true">
      <defs>
        <clipPath id="upper-blob">
          <ellipse cx="570" cy="115" rx="252" ry="160"/>
          <ellipse cx="640" cy="40" rx="262" ry="170"/>
        </clipPath>
      </defs>
      <ellipse cx="640" cy="420" rx="228" ry="215" fill="var(--flame-orange)"/>
      <ellipse cx="780" cy="400" rx="290" ry="300" fill="var(--flame-amber)" opacity="0.85"/>
      <ellipse cx="570" cy="115" rx="252" ry="160" fill="var(--flame-rust)"/>
      <ellipse cx="640" cy="40" rx="262" ry="170" fill="var(--flame-crimson)" opacity="0.85"/>
      <ellipse cx="780" cy="400" rx="330" ry="330" fill="var(--flame-deep)" opacity="0.7" clip-path="url(#upper-blob)"/>
    </svg>

    <div class="brand">
      <span class="brand-dot"></span>
      <span class="brand-name">VALCORNE</span>
    </div>

    <div class="person">
      <p class="person-name">Marla Tenwick</p>
      <p class="person-role">CEO</p>
    </div>

    <ul class="contacts">
      <li>
        <svg viewBox="0 0 20 16"><path d="M1 5 Q10 -1 19 5 L16 7 L14 4 L6 4 L4 7 Z M5 8 L15 8 L18 15 L2 15 Z"/></svg>
        (512)638-2974
      </li>
      <li>
        <svg viewBox="0 0 20 16"><path d="M1 2 H19 V14 H1 Z M2 3 L10 9 L18 3 Z" fill-rule="evenodd"/></svg>
        email-marla@valcorne.com
      </li>
      <li>
        <svg viewBox="0 0 20 16"><circle cx="10" cy="8" r="7" fill="none" stroke="var(--brand-red-text)" stroke-width="1.2"/><ellipse cx="10" cy="8" rx="3" ry="7" fill="none" stroke="var(--brand-red-text)" stroke-width="1.2"/><path d="M3 8 H17" stroke="var(--brand-red-text)" stroke-width="1.2"/></svg>
        website- valcorne.com
      </li>
    </ul>
  </section>

  <section class="card card-back" aria-label="Business card back">
    <div class="back-mark">
      <span class="back-dot"></span>
      <span class="back-name">VALCORNE</span>
    </div>
  </section>
</body>
</html>
```